Stationery Design Project

I need a stationary design for our company. we are based in Houston, TX and we are called Mira Vell Lending. And we are wanting to brand our MoneyMendPlus program, which includes our tax preparation and restoration, credit repair service. Although our business offers other programs, we are interested in mainly focusing on The MoneyMendPlus program. We are looking for way to brand our ourselves and I believe that a great stationery design will help in achieving this goal. Our logo design is blue and light blue. the slogan is orange.

Industry/Entity Type

Business

Requirements
Must have
• Address: 30871 Calloway Ln. B-22
Houston, TX 75419
Tel. 555-318-6207
Fax 555-294-7153
www.miravelllending.example
info@miravelllending.example
Our Slogan: Confidence, Renewed!

```html
<!DOCTYPE html>
<html lang="en">
<head>
<meta charset="utf-8">
<title>Mira Vell Lending – Business Card</title>
<link href="https://fonts.googleapis.com/css2?family=Tinos:wght@400;700&display=swap" rel="stylesheet">
<style>
  :root {
    --backdrop: #e9e4dc;
    --card-white: #ffffff;
    --navy: #153f66;
    --navy-edge: #0e2f4f;
    --brand-blue: #1d5c96;
    --slogan-orange: #f0961e;
    --ink: #333333;
    --square-border: #9fb8cf;
    --on-navy: #ffffff;
  }
  * { box-sizing: border-box; margin: 0; padding: 0; }
  html, body {
    width: 1200px; height: 381px; overflow: hidden;
    background: var(--backdrop);
    font-family: "Tinos", "Times New Roman", serif;
  }
  .canvas { position: relative; width: 1200px; height: 381px; }

  .card { position: absolute; border-radius: 26px; overflow: hidden; }

  .card--front {
    left: 22px; top: 40px; width: 538px; height: 316px;
    background: var(--card-white);
    border: 1px solid #555;
  }
  .brand-name {
    position: absolute; left: 34px; top: 88px;
    font-size: 37px; font-weight: 400; color: var(--brand-blue);
    letter-spacing: -0.5px; white-space: nowrap;
  }
  .slogan {
    position: absolute; left: 48px; top: 137px;
    font-size: 17px; font-weight: 700; color: var(--slogan-orange);
    letter-spacing: 1.6px; white-space: nowrap;
  }
  .contact-list {
    position: absolute; left: 35px; top: 178px;
    list-style: none; font-size: 14px; color: var(--ink);
  }
  .contact-list li {
    display: flex; align-items: center; height: 22px;
  }
  .contact-list svg { width: 12px; height: 12px; margin-right: 6px; fill: var(--ink); }
  .address {
    position: absolute; left: 34px; top: 280px;
    font-size: 14px; color: var(--ink); white-space: nowrap;
  }
  .mini-mark {
    position: absolute; left: 410px; top: 174px; width: 117px; height: 117px;
    background: var(--navy); border: 3px solid var(--square-border);
    display: flex; align-items: flex-end; justify-content: center;
    padding-bottom: 18px;
  }
  .mini-mark span { color: var(--on-navy); font-size: 11px; white-space: nowrap; }

  .card--back {
    left: 614px; top: 38px; width: 564px; height: 315px;
    background: var(--navy);
    border: 1px solid var(--navy-edge);
  }
  .back-name {
    position: absolute; left: 0; right: 0; top: 128px; text-align: center;
    color: var(--on-navy); font-size: 34px; font-weight: 400; letter-spacing: 1px;
  }
  .back-url {
    position: absolute; left: 0; right: 0; top: 263px; text-align: center;
    color: var(--on-navy); font-size: 13px; letter-spacing: 2.2px;
  }
  .back-url strong { font-weight: 700; }
</style>
</head>
<body>
<main class="canvas">

  <section class="card card--front" aria-label="Business card front">
    <div class="brand-name">MoneyMendPlus</div>
    <div class="slogan">Confidence, Renewed!</div>

    <ul class="contact-list">
      <li>
        <svg viewBox="0 0 12 12" aria-hidden="true"><path d="M2.5 0.8 4.3 3 3.3 4.3c.7 1.6 2 2.9 4.4 4.4L9 7.7l2.2 1.8-.9 1.7C6 11.5.5 6 .8 1.7z"/></svg>
        555-318-6207
      </li>
      <li>
        <svg viewBox="0 0 12 12" aria-hidden="true"><path d="M3 1h5l1 2H3zM1 4h10v5H9v2H3V9H1zm3 3v3h4V7z"/></svg>
        555-294-7153
      </li>
      <li>
        <svg viewBox="0 0 12 12" aria-hidden="true"><path d="M1 3h10v7H1zm1 1 4 3 4-3z" fill-rule="evenodd"/></svg>
        info@miravelllending.example
      </li>
      <li>
        <svg viewBox="0 0 12 12" aria-hidden="true"><path d="M6 1a5 5 0 1 0 0 10A5 5 0 0 0 6 1zm0 1c.8 0 1.5 1.6 1.6 3.5H4.4C4.5 3.6 5.2 2 6 2zM2.1 6.5h1.3c.1 1.1.3 2 .7 2.8A4 4 0 0 1 2.1 6.5zm0-1A4 4 0 0 1 4.1 2.7c-.4.8-.6 1.7-.7 2.8zm2.3 1h3.2C7.5 8.4 6.8 10 6 10s-1.5-1.6-1.6-3.5zm4.2 0h1.3a4 4 0 0 1-2 2.8c.4-.8.6-1.7.7-2.8zm0-1c-.1-1.1-.3-2-.7-2.8a4 4 0 0 1 2 2.8z"/></svg>
        www.miravelllending.example
      </li>
    </ul>

    <p class="address">30871 Calloway Ln. B-22, Houston, TX 75419</p>

    <div class="mini-mark"><span>Mira Vell Lending</span></div>
  </section>

  <section class="card card--back" aria-label="Business card back">
    <div class="back-name">Mira Vell Lending</div>
    <p class="back-url">www.<strong>miravelllending</strong>.example</p>
  </section>

</main>
</body>
</html>
```